Request for Business Card Design

Hi. My name is Marlene, I am looking for a new business card design for my company, Quarrow Signal Instruments, LLC. I really like the design you did for Tarsel Venture and was hoping you could do something similar using our full logo and our mark. I am also open to any raised texture design using our mark. I have attached our full logo, which would need to be somewhere on the card, as well as the mark in both outline and full form, as well as our brand colors / guide. The card does not have to be white, as long as our logo and mark appear. I actually like darker colored business cards more, but am open to all options. If you are interested in working with me, please let me know. We would also take the business card design into letterhead design if you can do that.

```html
<!DOCTYPE html>
<html lang="en">
<head>
<meta charset="utf-8">
<title>Quarrow Signal Instruments – Business Card</title>
<link href="https://fonts.googleapis.com/css2?family=Open+Sans:wght@400;600;700&display=swap" rel="stylesheet">
<style>
  :root {
    --stage: #232323;
    --card: #1e1e21;
    --card-deep: #151517;
    --accent: #1b9cc9;
    --ink: #ffffff;
    --muted: #4a4a4e;
    --mark-hi: #3a3a3e;
    --mark-lo: #0c0c0d;
  }
  * { margin: 0; padding: 0; box-sizing: border-box; }
  html, body {
    width: 1200px; height: 780px; overflow: hidden;
    background: var(--stage);
    font-family: "Open Sans", Arial, sans-serif;
  }
  .canvas { position: relative; width: 1200px; height: 780px; }

  .card {
    position: absolute;
    width: 620px; height: 354px;
    background: var(--card);
    border-radius: 22px;
    box-shadow: 0 4px 0 var(--accent), 0 18px 30px rgba(0,0,0,.55);
    overflow: hidden;
  }
  .card--back { left: 40px; top: 30px; }
  .card--front { left: 540px; top: 396px; }

  /* back */
  .pattern-field {
    position: absolute; inset: 0;
    background: linear-gradient(200deg, #4a4a4e 0%, #29292c 35%, var(--card-deep) 70%);
  }
  .back-signature {
    position: absolute; right: 30px; bottom: 26px;
    display: flex; align-items: center; gap: 8px;
  }
  .back-signature .dot { width: 14px; height: 14px; border-radius: 50%; background: var(--accent); }
  .back-signature .name {
    font-weight: 600; font-size: 11px; letter-spacing: .06em;
    text-transform: uppercase; color: var(--muted);
  }

  /* front */
  .brand {
    position: absolute; left: 30px; top: 30px;
    display: flex; align-items: center; gap: 14px;
  }
  .brand .dot { width: 46px; height: 46px; border-radius: 50%; background: var(--accent); }
  .brand .name {
    font-weight: 600; font-size: 22px; letter-spacing: .04em;
    text-transform: uppercase; color: var(--muted); line-height: 1.05;
  }

  .holder {
    position: absolute; right: 44px; top: 26px; text-align: right;
  }
  .holder .person { font-weight: 700; font-size: 34px; color: var(--accent); line-height: 1; }
  .holder .role { font-weight: 400; font-size: 14px; color: var(--ink); margin-top: 2px; }
  .accent-bar {
    position: absolute; right: 0; top: 24px;
    width: 22px; height: 54px; background: var(--accent);
  }

  .mark-relief {
    position: absolute; right: 18px; top: 100px;
    width: 270px; height: 230px; border-radius: 115px 40px 115px 115px;
    background: radial-gradient(circle at 45% 30%, var(--mark-hi), var(--mark-lo) 75%);
  }

  .address {
    position: absolute; left: 40px; top: 186px;
    color: var(--ink); font-size: 14px; line-height: 1.3;
  }
  .contacts {
    position: absolute; left: 40px; top: 234px;
    list-style: none; color: var(--ink); font-size: 14px; line-height: 1.35;
  }
  .contacts li { display: flex; align-items: center; gap: 8px; }
  .contacts svg { width: 13px; height: 13px; fill: var(--accent); flex: none; }
</style>
</head>
<body>
<main class="canvas">

  <section class="card card--back" aria-label="Card back">
    <div class="pattern-field" role="img" aria-label="Repeating brand-mark texture, fading from silver to black"></div>
    <div class="back-signature">
      <span class="dot"></span>
      <span class="name">Quarrow Signal Instruments</span>
    </div>
  </section>

  <section class="card card--front" aria-label="Card front">
    <div class="brand">
      <span class="dot"></span>
      <span class="name">Quarrow<br>Signal Instruments</span>
    </div>

    <span class="accent-bar"></span>
    <div class="holder">
      <p class="person">Marlene</p>
      <p class="role">Director</p>
    </div>

    <div class="mark-relief" role="img" aria-label="Large raised brand mark in black relief"></div>

    <address class="address">
      1180 Ledger Park Avenue<br>
      Alder Falls, CO 80999
    </address>

    <ul class="contacts">
      <li>
        <svg viewBox="0 0 24 24"><path d="M6.6 10.8a15 15 0 0 0 6.6 6.6l2.2-2.2c.3-.3.7-.4 1-.2 1.1.4 2.3.6 3.6.6.6 0 1 .4 1 1V20c0 .6-.4 1-1 1A17 17 0 0 1 3 4c0-.6.4-1 1-1h3.5c.6 0 1 .4 1 1 0 1.3.2 2.5.6 3.6.1.3 0 .7-.2 1z"/></svg>
        +001 555 010 2241
      </li>
      <li>
        <svg viewBox="0 0 24 24"><path d="M6 2h9l3 3v4H6zM3 10h18v9h-3v3H6v-3H3zm5 6v4h8v-4z"/></svg>
        +001 555 010 7730
      </li>
      <li>
        <svg viewBox="0 0 24 24"><path d="M12 2a10 10 0 1 0 0 20 10 10 0 0 0 0-20zm0 2c1 1.3 1.8 3.1 2.1 5H9.9C10.2 7.1 11 5.3 12 4zM4.3 11h3.6c0 .7 0 1.3.1 2H4.3a8 8 0 0 1 0-2zm5.6 0h4.2v2H9.9zm6.2 0h3.6a8 8 0 0 1 0 2H16zM9.9 15h4.2c-.3 1.9-1.1 3.7-2.1 5-1-1.3-1.8-3.1-2.1-5z"/></svg>
        www.quarrowsignal.com
      </li>
      <li>
        <svg viewBox="0 0 24 24"><path d="M2 5h20v14H2zm2 2v.5l8 5 8-5V7zm0 2.8V17h16V9.8l-8 5z"/></svg>
        info@quarrowsignal.com
      </li>
    </ul>
  </section>

</main>
</body>
</html>
```